Card Design for my dog training business Brightpaw Obedience

Need a business card design for my dog training business with my new logo. Want the card to come off professional yet fun. Want it to be very eye catchy as well. I normally have these at vet clinics, pet stores, and groomers. so need it to look better than my competitors.
Target Market(s)
dog owners
Industry/Entity Type
Dog Training
Contact Information for Business Card
needs logo, my name and info
Font styles to use
Serif
Colors
0255a3
ffffff
ec1f27
000000
333333
fbfbfb
Requirements
Must have
- Brightpaw Obedience
- Felix Orland
- 415 903 2276
- info@brightpawobedience.example
- www.brightpawobedience.example

```html
<!DOCTYPE html>
<html lang="en">
<head>
<meta charset="utf-8">
<title>Brightpaw Obedience — Business Card</title>
<link href="https://fonts.googleapis.com/css2?family=Noto+Serif:wght@400&family=EB+Garamond:ital@1&display=swap" rel="stylesheet">
<style>
  :root {
    --brand-blue: #0255a3;
    --card-blue: #034b94;
    --brand-red: #ec1f27;
    --ink: #333333;
    --black: #000000;
    --paper: #fbfbfb;
    --white: #ffffff;
    --backdrop: #c9c9c9;
    --art-light: #ececec;
    --art-mid: #d2d2d2;
  }
  * { box-sizing: border-box; margin: 0; padding: 0; }
  html, body { width: 1200px; height: 576px; overflow: hidden; }
  body {
    background: var(--backdrop);
    position: relative;
    font-family: "Noto Serif", Georgia, serif;
  }
  .card {
    position: absolute;
    top: 138px;
    width: 483px;
    height: 293px;
    border-radius: 12px;
    overflow: hidden;
    box-shadow: 0 3px 6px rgba(0,0,0,0.25);
  }
  /* Front */
  .card-front {
    left: 82px;
    background: linear-gradient(180deg, #05529c 0%, var(--card-blue) 100%);
  }
  .front-wordmark {
    position: absolute;
    top: 116px;
    left: 0; right: 0;
    text-align: center;
    color: var(--white);
    font-size: 24px;
    letter-spacing: 0.5px;
  }
  .front-band {
    position: absolute;
    left: 0; right: 0;
    top: 255px;
    height: 28px;
    background: var(--black);
    display: flex;
    align-items: center;
    justify-content: center;
  }
  .tagline {
    font-family: "EB Garamond", Georgia, serif;
    font-style: italic;
    font-size: 12px;
    color: var(--white);
  }
  /* Back */
  .card-back {
    left: 602px;
    background: var(--paper);
  }
  .back-wordmark {
    position: absolute;
    top: 34px;
    left: 20px;
    color: var(--brand-blue);
    font-size: 19px;
  }
  .back-rule {
    position: absolute;
    left: 20px;
    top: 66px;
    width: 186px;
    height: 2px;
    background: var(--brand-red);
  }
  .back-artwork {
    position: absolute;
    left: 266px;
    top: 22px;
    right: 0;
    bottom: 0;
    border-top-left-radius: 6px;
    background: linear-gradient(135deg, var(--art-light) 0%, var(--art-mid) 100%);
  }
  .holder-name {
    position: absolute;
    top: 163px;
    left: 20px;
    font-size: 19px;
    font-weight: 400;
    color: var(--brand-blue);
  }
  .holder-role {
    position: absolute;
    top: 190px;
    left: 20px;
    font-size: 11.5px;
    color: var(--ink);
  }
  .contact-list {
    position: absolute;
    top: 216px;
    left: 20px;
    list-style: none;
  }
  .contact-item {
    display: flex;
    align-items: center;
    gap: 10px;
    height: 20px;
    font-size: 11.5px;
    color: var(--ink);
    white-space: nowrap;
  }
  .contact-icon { width: 10px; height: 10px; fill: var(--ink); flex: none; }
</style>
</head>
<body>
  <section class="card card-front">
    <div class="front-wordmark">Brightpaw Obedience</div>
    <div class="front-band">
      <p class="tagline">“Training dogs across the Bay one dog at a time.”</p>
    </div>
  </section>

  <section class="card card-back">
    <div class="back-wordmark">Brightpaw Obedience</div>
    <div class="back-rule"></div>
    <div class="back-artwork" role="img" aria-label="Large line illustration of two dogs within a state outline"></div>
    <h1 class="holder-name">Felix Orland</h1>
    <p class="holder-role">Dog Trainer</p>
    <ul class="contact-list">
      <li class="contact-item">
        <svg class="contact-icon" viewBox="0 0 10 10" aria-hidden="true"><path d="M1 4 Q5 0 9 4 L8 5 L6.5 4 L6.5 3.3 Q5 2.8 3.5 3.3 L3.5 4 L2 5 Z M2.5 5.5 H7.5 L8.5 9 H1.5 Z"/></svg>
        <span>415 903 2276</span>
      </li>
      <li class="contact-item">
        <svg class="contact-icon" viewBox="0 0 10 10" aria-hidden="true"><path d="M0.5 2 H9.5 V8.5 H0.5 Z M1.3 2.6 L5 5.6 L8.7 2.6" fill="none" stroke="#333333" stroke-width="1.1"/></svg>
        <span>info@brightpawobedience.example</span>
      </li>
      <li class="contact-item">
        <svg class="contact-icon" viewBox="0 0 10 10" aria-hidden="true"><circle cx="5" cy="5" r="4.3" fill="none" stroke="#333333" stroke-width="1"/><ellipse cx="5" cy="5" rx="1.8" ry="4.3" fill="none" stroke="#333333" stroke-width="0.9"/><path d="M0.7 5 H9.3" stroke="#333333" stroke-width="0.9"/></svg>
        <span>www.brightpawobedience.example</span>
      </li>
    </ul>
  </section>
</body>
</html>
```